Re-Design my old Business Card

We need a new business card design. The current layout is lacking good design.
We manufacture building products and also offers services (www.tqconstructlabs.com.au)
I've attached the old business card to show you what we don't want.
I've also attached the new logo in two styles for you to chose from.
The final design should communicate smarter building design and lifestyle, with a clean and crisp designed card.

Target Market(s)

Architects, building companies

Industry/Entity Type

Business

Contact Information for Business Card

See attached old business cards for all details to include

Font styles to use
Sans Serif

Colors
9bcb3b

Requirements
Must have
• Clean crisp look
Nice to have
• Totally up to you

```html
<!DOCTYPE html>
<html lang="en">
<head>
<meta charset="utf-8">
<title>TQ Construct Labs – Business Card</title>
<link href="https://fonts.googleapis.com/css2?family=Lato:wght@400;700;900&display=swap" rel="stylesheet">
<style>
  :root {
    --green: #9bcb3b;
    --ink: #4a4a4a;
    --paper: #ffffff;
    --paper-shade: #eeeeee;
    --charcoal: #2b2b2b;
    --charcoal-light: #3a3a3a;
    --backdrop: #1a1a1a;
    --light: #f2f2f2;
  }
  * { margin: 0; padding: 0; box-sizing: border-box; }
  html, body { width: 1200px; height: 873px; overflow: hidden; }
  body {
    background: var(--backdrop);
    font-family: "Lato", sans-serif;
    position: relative;
  }
  .card {
    position: absolute;
    width: 560px;
    height: 320px;
    overflow: hidden;
    box-shadow: 0 14px 40px rgba(0,0,0,.6);
  }

  /* Front */
  .card-front {
    left: 110px; top: 80px;
    background: linear-gradient(180deg, var(--paper) 0%, var(--paper-shade) 100%);
  }
  .front-brand {
    position: absolute; left: 130px; top: 62px;
    display: flex; align-items: center; gap: 10px;
  }
  .front-brand .brand-mark { width: 18px; height: 18px; background: var(--green); flex: none; }
  .front-brand .brand-name {
    color: var(--green); font-weight: 900; font-size: 22px; letter-spacing: .5px;
    text-transform: uppercase; line-height: 1.1; width: 160px;
  }
  .holder {
    position: absolute; right: 28px; top: 38px; text-align: right; color: var(--ink); font-size: 11px; line-height: 1.5;
  }
  .holder .person { color: var(--green); font-weight: 700; font-size: 15px; }
  .holder .office-label { text-decoration: underline; margin-top: 4px; }
  .holder .address { color: var(--green); font-weight: 700; font-size: 12px; }
  .front-swoosh { position: absolute; left: 0; top: 0; width: 560px; height: 320px; }
  .contact-tab {
    position: absolute; left: 0; bottom: 20px; width: 36px; height: 116px;
    background: var(--green); border-radius: 0 8px 8px 0;
    display: flex; flex-direction: column; justify-content: space-around; align-items: center; padding: 6px 0;
  }
  .contact-tab svg { width: 14px; height: 14px; fill: var(--paper); }
  .contact-list {
    position: absolute; left: 50px; bottom: 26px; list-style: none; color: var(--ink); font-size: 14px; line-height: 26px;
  }

  /* Back */
  .card-back {
    left: 530px; top: 470px;
    background: linear-gradient(135deg, var(--charcoal-light) 0%, var(--charcoal) 55%, #222 100%);
  }
  .back-texture {
    position: absolute; inset: 0;
    background: linear-gradient(160deg, rgba(255,255,255,.05), rgba(0,0,0,.1));
  }
  .back-brand {
    position: absolute; left: 0; right: 0; top: 118px;
    display: flex; justify-content: center; align-items: center; gap: 14px;
  }
  .back-brand .brand-mark { width: 24px; height: 24px; background: var(--light); flex: none; }
  .back-brand .brand-name {
    color: var(--light); font-weight: 900; font-size: 32px; letter-spacing: 1px; text-transform: uppercase;
  }
  .back-web {
    position: absolute; left: 0; right: 0; bottom: 44px; text-align: center;
    color: var(--light); font-weight: 700; font-size: 16px; letter-spacing: .5px;
  }
</style>
</head>
<body>

<section class="card card-front">
  <svg class="front-swoosh" viewBox="0 0 560 320" aria-hidden="true">
    <path d="M0 305 L330 305 C345 305 350 288 372 288 L560 288 L560 320 L0 320 Z" fill="#d9d9d9"/>
    <path d="M352 305 C365 305 368 280 392 280 L560 280 L560 300 L352 305 Z" fill="var(--green)"/>
  </svg>

  <div class="front-brand">
    <span class="brand-mark"></span>
    <span class="brand-name">TQ Construct Labs</span>
  </div>

  <div class="holder">
    <div class="person">Marcus Hale</div>
    <div class="role">Account Manager Qld / Northern NSW</div>
    <div class="office-label">Head Office:</div>
    <div class="address">Unit 4/27 Harlow Street</div>
    <div class="address">Ridgefield, QLD 4130</div>
  </div>

  <div class="contact-tab">
    <svg viewBox="0 0 16 16" aria-label="Phone"><path d="M1 4c0-2 2-3 4-3l1 3-2 1c0 2 3 5 5 5l1-2 3 1c0 2-1 4-3 4C5 13 1 9 1 4z"/></svg>
    <svg viewBox="0 0 16 16" aria-label="Mobile"><path d="M4 1h8v14H4zM5 3v9h6V3z"/></svg>
    <svg viewBox="0 0 16 16" aria-label="Fax"><path d="M4 1h8v4H4zM1 6h14v7h-3v2H4v-2H1zM5 10v4h6v-4z"/></svg>
    <svg viewBox="0 0 16 16" aria-label="Email"><path d="M1 3h14v10H1zM2 4l6 5 6-5z"/></svg>
  </div>
  <ul class="contact-list">
    <li>1300 555 210</li>
    <li>0400 555 827</li>
    <li>1300 555 211</li>
    <li>marcus@tqconstructlabs.com.au</li>
  </ul>
</section>

<section class="card card-back">
  <div class="back-texture" role="img" aria-label="Faint low-poly geometric texture in dark grey"></div>
  <div class="back-brand">
    <span class="brand-mark"></span>
    <span class="brand-name">TQ Construct Labs</span>
  </div>
  <div class="back-web">www.tqconstructlabs.com.au</div>
</section>

</body>
</html>
```